Automotive Accessories Business Card

Design a business template that match our new logo design and our industry.

https://www.qelmotorgear.com/

Target Market(s)

Aftermarket auto parts and accessories

Industry/Entity Type

automotive

Contact Information for Business Card

company logo

Font styles to use
Serif
Sans Serif

Colors
EB3D1F
EC4F4E
F09395
F8D3D4
FCEDEE

```html
<!DOCTYPE html>
<html lang="en">
<head>
<meta charset="utf-8">
<title>QEL Motor Gear — Business Card</title>
<link rel="stylesheet" href="https://fonts.googleapis.com/css2?family=Arimo:wght@400;700&display=swap">
<style>
  :root {
    --red: #e0212b;
    --charcoal: #3a393b;
    --charcoal-deep: #2b2a2c;
    --ink: #1e1e1e;
    --paper: #ffffff;
    --stage: #d9d9d9;
    --rule: #6a6a6a;
  }
  * { box-sizing: border-box; margin: 0; padding: 0; }
  html, body { width: 1200px; height: 800px; overflow: hidden; }
  body {
    background: var(--stage);
    font-family: "Arimo", Arial, sans-serif;
    display: flex;
    align-items: center;
    justify-content: center;
    gap: 40px;
  }
  .card {
    width: 540px;
    height: 310px;
    position: relative;
    overflow: hidden;
    border-bottom: 3px solid var(--red);
    box-shadow: 0 10px 24px rgba(0,0,0,0.18);
  }
  /* Front */
  .card--front { background: var(--paper); }
  .front__brand {
    position: absolute;
    left: 40px;
    top: 0;
    width: 230px;
    height: 250px;
    display: flex;
    align-items: center;
    gap: 10px;
  }
  .brand-mark {
    width: 18px;
    height: 18px;
    background: var(--red);
    flex: none;
  }
  .brand-name {
    font-weight: 700;
    font-size: 24px;
    color: var(--red);
    letter-spacing: 0.5px;
  }
  .front__divider {
    position: absolute;
    left: 280px;
    top: 70px;
    width: 1px;
    height: 110px;
    background: var(--rule);
  }
  .contact {
    position: absolute;
    left: 300px;
    top: 64px;
    color: var(--ink);
  }
  .contact__name {
    font-weight: 700;
    font-size: 17px;
    color: var(--red);
    letter-spacing: 0.5px;
  }
  .contact__title { font-size: 14px; margin-bottom: 8px; }
  .contact__line {
    display: flex;
    align-items: center;
    gap: 6px;
    font-size: 13.5px;
    line-height: 21px;
  }
  .contact__line svg { width: 12px; height: 12px; flex: none; }
  .accent { color: var(--red); }
  .front__band {
    position: absolute;
    left: 0; right: 0; bottom: 0;
    height: 57px;
    background: var(--charcoal);
    display: flex;
    align-items: center;
    gap: 8px;
    padding-left: 36px;
    color: var(--paper);
    font-size: 15px;
    letter-spacing: 0.3px;
  }
  .front__band svg { width: 12px; height: 16px; }
  /* Back */
  .card--back { background: var(--charcoal-deep); }
  .back__pattern {
    position: absolute;
    inset: 0;
    background: linear-gradient(135deg, #2a292b 0%, #3d3c3e 55%, #565557 100%);
  }
  .back__brand {
    position: absolute;
    left: 50%;
    top: 50%;
    transform: translate(-50%, -50%);
    display: flex;
    align-items: center;
    gap: 8px;
  }
  .back__brand .brand-name { color: var(--paper); font-size: 20px; }
  .back__brand .brand-mark { width: 14px; height: 14px; }
</style>
</head>
<body>
  <section class="card card--front">
    <div class="front__brand">
      <span class="brand-mark"></span>
      <span class="brand-name">QEL MOTOR GEAR</span>
    </div>
    <div class="front__divider"></div>
    <div class="contact">
      <p class="contact__name">MARCUS HALE</p>
      <p class="contact__title">Managing Director</p>
      <p class="contact__line">
        <svg viewBox="0 0 12 12"><path d="M3 1 L5 3.5 L4 5 Q5 7 7 8 L8.5 7 L11 9 L9.5 11 Q5 11 1 5 Z" fill="var(--red)"/></svg>
        044-987 654 321
      </p>
      <p class="contact__line">
        <svg viewBox="0 0 12 12"><rect x="1" y="2.5" width="10" height="7" fill="var(--red)"/><path d="M1 2.5 L6 6.5 L11 2.5" stroke="#fff" fill="none"/></svg>
        info@qelmotorgear.com
      </p>
      <p class="contact__line">
        <svg viewBox="0 0 12 12"><circle cx="6" cy="6" r="5" fill="var(--red)"/><path d="M1 6 H11 M6 1 V11" stroke="#fff" stroke-width="0.8"/></svg>
        www.<span class="accent">qelmotorgear</span>.com
      </p>
    </div>
    <div class="front__band">
      <svg viewBox="0 0 12 16"><path d="M6 16 L1.5 8 A5 5 0 1 1 10.5 8 Z" fill="var(--red)"/><circle cx="6" cy="5.5" r="2" fill="var(--charcoal)"/></svg>
      218, Harbor Lane Suite 4, 45452, Country Name
    </div>
  </section>

  <section class="card card--back">
    <div class="back__pattern" role="img" aria-label="Tone-on-tone repeating brand pattern on dark grey"></div>
    <div class="back__brand">
      <span class="brand-mark"></span>
      <span class="brand-name">QEL MOTOR GEAR</span>
    </div>
  </section>
</body>
</html>
```